Social Media Templates for Fieldhouse Raffle Fund

We need a set of Square (1080 x 1080) social media posts.

My company works with sports clubs, helping them to raise money with a lottery.

I need a set of social media image that I can use to appeal to new Fieldhouse Raffle Fund to encourage them to start a lottery with us.

This landing page has worked very well for us https://fieldhouserafflefund.com/fieldhouse-raffle-fund/

THING THAT APPEAL TO CLUBS

No Setup Fees/Start for Free - (We don’t charge any registration fees, or setup fees so you can start raising money from the first draw.)

Start Straight Away - (A club can start raising money straight away.)

Sustainable Income - (The average player plays for 7 years)

Subscription Lottery - (once a player joins, they play until the choose to leave. A club doesn't have to sell tickets every draw to the same people)

All Administration Taken Care Of - (We do all the hard work, so they can focus on running their club.)

Unlimited Income - (There is no limit on the amount of money a club can raise: the more players, the more funds for the club.)

Fundraising reach - (Reach new fans)

50% of the sales is guaranteed profit

£25,000 jackpot - (a person could win £25,000 every week)

Price - (It costs just £1 per week to enter)

Help Your Club - (100% of the profit goes to the club who a player chooses to support)

You can see all the clubs we work with on www.fieldhouserafflefund.com

The images will also be used on Chatterwall. You can see some examples here https://www.chatterwall.com/FieldhouseRaffleFund/ (you may need a proxy to view this page as it is only viewable in the UK, so I have attached some screenshots)

You can find the Fieldhouse Raffle Fund Logo here https://www.logovault.com/winwellgroup/

Target Market(s)

People who are involved with amateur sports in United Kingdom

Industry/Entity Type

Gambling

Font styles to use
Sans Serif

Requirements
Must have
• My project must look great on social social media and encourage people to get in touch about starting a lottery with us.

Adobe Suite files must be provided

```html
<!DOCTYPE html>
<html lang="en">
<head>
<meta charset="utf-8">
<title>Fieldhouse Raffle Fund – Win £25,000</title>
<link rel="stylesheet" href="https://fonts.googleapis.com/css2?family=Bitter:ital,wght@0,500;0,700;0,900;1,800&display=swap">
<style>
  :root {
    --sky-blue: #2b80c0;
    --sky-blue-light: #5aa5d8;
    --banner-orange: #ff6600;
    --cream: #fff7e0;
    --sun-yellow: #f8ff2a;
    --deep-red: #7a1a08;
    --white: #ffffff;
    --photo-top: #c9a48a;
    --photo-mid: #e4e0d8;
    --photo-bottom: #9ccf2e;
  }
  html, body {
    margin: 0;
    padding: 0;
    width: 1200px;
    height: 1200px;
    overflow: hidden;
    background: var(--sky-blue);
  }
  .post {
    position: relative;
    width: 1200px;
    height: 1200px;
    background: var(--sky-blue);
    overflow: hidden;
    font-family: "Bitter", serif;
  }
  .backdrop {
    position: absolute;
    inset: 0;
  }
  .photo {
    position: absolute;
    left: 0;
    top: 399px;
    width: 640px;
    height: 801px;
  }
  .brand-mark {
    position: absolute;
    left: 39px;
    top: 48px;
    width: 337px;
    height: 286px;
    display: flex;
    align-items: center;
    justify-content: center;
    gap: 14px;
  }
  .brand-mark__square {
    width: 26px;
    height: 26px;
    background: var(--white);
    flex: none;
  }
  .brand-mark__name {
    color: var(--white);
    font-weight: 700;
    font-size: 38px;
    line-height: 1.1;
  }
  .headline {
    position: absolute;
    top: 0;
    left: 380px;
    width: 830px;
    height: 399px;
    margin: 0;
    text-align: center;
  }
  .headline__lead {
    font-style: italic;
    font-weight: 800;
    font-size: 46px;
    color: var(--cream);
    text-shadow: 2px 2px 0 var(--deep-red), 3px 4px 4px rgba(0,0,0,.35);
    line-height: 1;
  }
  .headline__lead--top { position: absolute; top: 64px; left: 0; right: 0; }
  .headline__lead--mid {
    position: absolute; top: 133px; left: 0; right: 0;
    display: flex; align-items: center; justify-content: center; gap: 24px;
  }
  .rule {
    width: 132px;
    height: 2px;
    background: var(--cream);
  }
  .headline__prize {
    position: absolute;
    top: 196px;
    left: 0; right: 0;
    font-weight: 900;
    font-size: 104px;
    line-height: 1.1;
    color: var(--sun-yellow);
    background: linear-gradient(180deg, var(--cream) 15%, var(--sun-yellow) 75%);
    -webkit-background-clip: text;
    background-clip: text;
    -webkit-text-fill-color: transparent;
    -webkit-text-stroke: 3px var(--deep-red);
    filter: drop-shadow(3px 6px 5px rgba(80,10,0,.55));
  }
  .benefit {
    position: absolute;
    left: 698px;
    top: 478px;
    margin: 0;
    color: var(--white);
    font-weight: 700;
    font-size: 30px;
    line-height: 44px;
  }
  .benefit__highlight {
    display: block;
    color: var(--sun-yellow);
    margin-bottom: 14px;
  }
  .benefit__underline {
    position: absolute;
    left: 691px;
    top: 516px;
  }
  .join-button {
    position: absolute;
    left: 700px;
    top: 661px;
    width: 261px;
    height: 64px;
    border-radius: 8px;
    background: linear-gradient(180deg, #ff8d35, var(--banner-orange));
    box-shadow: 0 3px 4px rgba(0,0,0,.25);
    color: var(--white);
    font-weight: 500;
    font-size: 40px;
    line-height: 64px;
    text-align: center;
    text-decoration: none;
  }
  .partner {
    position: absolute;
    color: var(--white);
    font-weight: 700;
    text-align: center;
    line-height: 1.05;
    font-size: 36px;
  }
  .partner--skyline {
    left: 950px;
    top: 880px;
    width: 190px;
  }
  .partner--winwell {
    left: 950px;
    top: 1030px;
    width: 190px;
  }
</style>
</head>
<body>
  <main class="post">
    <svg class="backdrop" width="1200" height="1200" viewBox="0 0 1200 1200" aria-hidden="true">
      <path d="M290 0 L339 0 L150 399 L110 399 Z" fill="var(--sky-blue-light)" opacity=".6"/>
      <path d="M339 0 H1200 V399 H170 Q130 399 145 365 Z" fill="var(--banner-orange)"/>
    </svg>

    <svg class="photo" viewBox="0 0 640 801" preserveAspectRatio="none" role="img" aria-label="Photo of a smiling child in a lime green t-shirt holding a football">
      <defs>
        <linearGradient id="photoTone" x1="0" y1="0" x2="0" y2="1">
          <stop offset="0" stop-color="var(--sky-blue)"/>
          <stop offset=".12" stop-color="var(--photo-top)"/>
          <stop offset=".5" stop-color="var(--photo-mid)"/>
          <stop offset=".8" stop-color="var(--photo-bottom)"/>
          <stop offset="1" stop-color="var(--photo-bottom)"/>
        </linearGradient>
      </defs>
      <rect x="0" y="0" width="640" height="801" fill="url(#photoTone)"/>
    </svg>

    <div class="brand-mark">
      <span class="brand-mark__square"></span>
      <span class="brand-mark__name">Fieldhouse<br>Raffle Fund</span>
    </div>

    <h1 class="headline">
      <span class="headline__lead headline__lead--top">Support a Local Sports Club</span>
      <span class="headline__lead headline__lead--mid"><span class="rule"></span>and You Could<span class="rule"></span></span>
      <span class="headline__prize">Win £25,000</span>
    </h1>

    <p class="benefit">
      <span class="benefit__highlight">100% of the profit</span>
      goes to the club who a<br>player chooses to support
    </p>
    <svg class="benefit__underline" width="320" height="16" viewBox="0 0 320 16" aria-hidden="true">
      <path d="M2 12 Q150 0 318 8" stroke="var(--sun-yellow)" stroke-width="3" fill="none" stroke-linecap="round"/>
    </svg>

    <a class="join-button" href="https://fieldhouserafflefund.com/fieldhouse-raffle-fund/">Join now</a>

    <div class="partner partner--skyline">Skyline<br>Draw</div>
    <div class="partner partner--winwell">Winwell<br>Group</div>
  </main>
</body>
</html>
```